Realtor branding business card

modern, simple and self branding. Broker office logo needs to be used but not emphasized. Looking to brand myself

Target Market(s)

buyers, sellers and investors

Industry/Entity Type

Realtor

Contact Information for Business Card

Sample of my current business card on file

Requirements
Must have
• my website - tobiasmerrowkl.com
• Realtor logo
• Fair housing logo
Nice to have
• Colors from office logo but not a must
Should not have
• Do not want headshot

```html
<!DOCTYPE html>
<html lang="en">
<head>
<meta charset="utf-8">
<title>The Merrow Group – Business Card</title>
<link href="https://fonts.googleapis.com/css2?family=Arimo:wght@400;700&display=swap" rel="stylesheet">
<style>
  :root {
    --page-bg: #ecebe8;
    --card-light-1: #fafafa;
    --card-light-2: #d9d9d9;
    --card-dark-1: #6d7075;
    --card-dark-2: #45474b;
    --ink: #2b2b2b;
    --ink-soft: #555555;
    --accent-red: #d3272b;
    --accent-orange: #e8835a;
    --skyline: #bdbdbd;
    --white: #ffffff;
  }
  * { box-sizing: border-box; margin: 0; padding: 0; }
  html, body { width: 800px; height: 1200px; overflow: hidden; }
  body {
    background: var(--page-bg);
    font-family: "Arimo", Arial, sans-serif;
    position: relative;
  }

  /* ---------- Front card ---------- */
  .card-front {
    position: absolute;
    left: 225px; top: 50px;
    width: 350px; height: 560px;
    border-radius: 22px;
    background: radial-gradient(ellipse at 55% 35%, var(--card-light-1), var(--card-light-2));
    overflow: hidden;
    box-shadow: 0 8px 22px rgba(0,0,0,.18);
    color: var(--ink);
    text-align: center;
  }
  .brand-name {
    margin-top: 58px;
    display: flex; align-items: center; justify-content: center; gap: 10px;
    font-weight: 700; font-size: 30px; letter-spacing: 4px; color: var(--ink);
  }
  .brand-square { width: 12px; height: 12px; background: var(--accent-red); }
  .brand-rule {
    width: 200px; height: 2px; margin: 12px auto 0;
    background: linear-gradient(90deg, transparent, var(--accent-red), transparent);
  }
  .agent-name {
    margin-top: 36px;
    font-weight: 700; font-size: 22px; color: var(--ink-soft); letter-spacing: .5px;
  }
  .agent-title { font-size: 15px; color: var(--accent-red); margin-top: 2px; }

  .contact-list { margin-top: 26px; list-style: none; }
  .contact-item { margin-bottom: 12px; font-size: 15px; color: var(--ink); line-height: 1.3; }
  .contact-icon {
    display: block; margin: 0 auto 4px;
    width: 22px; height: 22px;
  }
  .contact-rule {
    width: 240px; height: 1px; margin: 6px auto 14px;
    background: linear-gradient(90deg, transparent, var(--accent-orange), transparent);
  }

  .skyline-band {
    position: absolute; left: 0; right: 0; bottom: 22px; height: 110px;
    background: linear-gradient(180deg, rgba(189,189,189,0) 0%, var(--skyline) 55%, #d0d0d0 100%);
  }
  .front-website {
    position: absolute; left: 0; right: 0; bottom: 36px;
    font-weight: 700; font-size: 16px; color: var(--ink);
  }
  .front-edge {
    position: absolute; left: 0; right: 0; bottom: 0; height: 14px;
    background: var(--accent-red);
  }

  /* ---------- Back card ---------- */
  .card-back {
    position: absolute;
    left: 120px; top: 700px;
    width: 560px; height: 350px;
    border-radius: 22px;
    background: radial-gradient(ellipse at 50% 30%, var(--card-dark-1), var(--card-dark-2));
    box-shadow: 0 8px 22px rgba(0,0,0,.25);
    color: var(--white);
    display: flex; flex-direction: column; align-items: center; justify-content: center;
  }
  .office-name {
    display: flex; align-items: center; gap: 14px;
    font-weight: 700; font-size: 38px; color: var(--white); line-height: 1;
  }
  .office-square { width: 22px; height: 22px; background: var(--white); }
  .office-website {
    margin-top: 30px;
    font-size: 15px; letter-spacing: 5px; color: #e4e4e4;
  }
</style>
</head>
<body>

  <section class="card-front">
    <div class="brand-name"><span class="brand-square"></span>THE MERROW GROUP</div>
    <div class="brand-rule"></div>

    <h1 class="agent-name">TOBIAS MERROW, PA</h1>
    <p class="agent-title">Realtor</p>

    <ul class="contact-list">
      <li class="contact-item">
        <svg class="contact-icon" viewBox="0 0 22 22"><circle cx="11" cy="11" r="10" fill="#fff" stroke="#888"/><rect x="7.5" y="5.5" width="7" height="11" rx="1.2" fill="none" stroke="#333" stroke-width="1.4"/></svg>
        555.214.0387
      </li>
      <li class="contact-item">
        <svg class="contact-icon" viewBox="0 0 22 22"><circle cx="11" cy="11" r="10" fill="#fff" stroke="#888"/><rect x="6" y="7.5" width="10" height="7" fill="none" stroke="#333" stroke-width="1.4"/><path d="M6 7.5l5 4 5-4" fill="none" stroke="#333" stroke-width="1.2"/></svg>
        merrowrealty@mail.com
      </li>
    </ul>
    <div class="contact-rule"></div>
    <ul class="contact-list" style="margin-top:0">
      <li class="contact-item">
        <svg class="contact-icon" viewBox="0 0 22 22"><circle cx="11" cy="11" r="10" fill="#fff" stroke="#888"/><path d="M11 17s-4-4.5-4-7.5a4 4 0 0 1 8 0C15 12.5 11 17 11 17z" fill="none" stroke="#333" stroke-width="1.4"/><circle cx="11" cy="9.5" r="1.3" fill="#333"/></svg>
        48 Larkspur Ave.<br>Cedar Hollow, FL 32901<br>555.310.4400
      </li>
    </ul>

    <div class="skyline-band" role="img" aria-label="Grey city skyline silhouette"></div>
    <p class="front-website">www.tobiasmerrowkl.com</p>
    <div class="front-edge"></div>
  </section>

  <section class="card-back">
    <div class="office-name"><span class="office-square"></span>Hearthline Realty Group</div>
    <p class="office-website">www.hearthlinefl.com</p>
  </section>

</body>
</html>
```